Modern Business Card for Larkwell 2018

Our company assumes the best about people. We are creating an online community of entrepreneurs and business leaders who struggle with marketing their business online.

This business card should POP! We recently got a new logo and are launching a new website next month, so our business cards should make a statement that feels:
-Fresh
-Smart
-Trustworthy
-Fun

Target Market(s)

small business owners, entrepreneurs

Industry/Entity Type

Digital Marketing

Contact Information for Business Card

Dimensions: 3.5" x 2"

Font styles to use
Sans Serif

Colors
f37122
ffffff

Requirements
Must have
• We need a business card with a modern, bold design. We will use one side of the card as a lead-generation offer, so text on one side will need to fit up to 140 characters. The business card should stick to our core colors (orange, black, and white).
Nice to have
• We think a vertical "portrait" design could be interesting.
Should not have
• Should not look like a traditional business card. The round icon should stand out from a distance.

```html
<!DOCTYPE html>
<html lang="en">
<head>
<meta charset="utf-8">
<title>Larkwell Business Card</title>
<link rel="stylesheet" href="https://fonts.googleapis.com/css2?family=Roboto:wght@400;500;700&display=swap">
<style>
  :root {
    --brand-orange: #f26a28;
    --ink: #222222;
    --paper: #f3f3f3;
    --backdrop: #dcdcdc;
    --white: #ffffff;
  }
  * { margin: 0; padding: 0; box-sizing: border-box; }
  html, body {
    width: 1200px; height: 960px; overflow: hidden;
    background: var(--backdrop);
    font-family: "Roboto", Arial, sans-serif;
  }
  .canvas { position: relative; width: 1200px; height: 960px; }

  .card { position: absolute; width: 600px; background: var(--paper); overflow: hidden; }

  /* Front */
  .card-front { left: 302px; top: 118px; height: 343px; }
  .front-mark {
    position: absolute; right: 58px; top: 64px;
    display: flex; align-items: center; gap: 8px;
  }
  .front-mark .dot { width: 22px; height: 22px; border-radius: 50%; background: var(--brand-orange); }
  .front-mark .name { color: var(--brand-orange); font-weight: 700; font-size: 16px; letter-spacing: 1px; }
  .person { position: absolute; left: 53px; top: 248px; }
  .person-name { color: var(--brand-orange); font-weight: 500; font-size: 23px; letter-spacing: -0.2px; line-height: 1.1; }
  .person-title { color: var(--ink); font-size: 16px; margin-top: 3px; letter-spacing: 0.2px; }
  .front-divider { position: absolute; left: 296px; top: 248px; width: 2px; height: 44px; background: var(--brand-orange); }
  .person-email { position: absolute; left: 326px; top: 274px; color: var(--ink); font-size: 16px; }

  /* Back */
  .card-back { left: 299px; top: 499px; height: 343px; }
  .offer-band { position: absolute; left: 0; top: 0; width: 600px; height: 218px; background: var(--brand-orange); color: var(--white); }
  .brand-lockup { position: absolute; left: 46px; top: 60px; width: 226px; text-align: center; }
  .brand-lockup .dot { width: 38px; height: 38px; border-radius: 50%; background: var(--white); margin: 0 auto 12px; }
  .brand-lockup .name { font-weight: 700; font-size: 36px; letter-spacing: 1.5px; line-height: 1; }
  .tagline-lettering { display: block; width: 224px; height: 10px; margin: 8px auto 0; background: rgba(255,255,255,0.55); border-radius: 2px; }
  .band-divider { position: absolute; left: 297px; top: 28px; width: 1px; height: 165px; background: rgba(255,255,255,0.7); }
  .offer { position: absolute; left: 323px; top: 29px; }
  .offer-headline { font-weight: 700; font-size: 20px; line-height: 21px; text-transform: uppercase; }
  .offer-body { font-size: 15.5px; line-height: 19.5px; margin-top: 6px; }
  .offer-url { font-weight: 700; font-size: 20px; margin-top: 8px; }
  .note-line { position: absolute; left: 36px; width: 520px; height: 1px; background: var(--ink); }
  .note-line.first { top: 260px; }
  .note-line.second { top: 300px; }
</style>
</head>
<body>
<main class="canvas">
  <section class="card card-front">
    <div class="front-mark"><span class="dot"></span><span class="name">LARKWELL</span></div>
    <div class="person">
      <div class="person-name">DANA WHITFIELD</div>
      <div class="person-title">STORY MARKETING COACH</div>
    </div>
    <div class="front-divider"></div>
    <div class="person-email">dana@larkwellnow.com</div>
  </section>

  <section class="card card-back">
    <div class="offer-band">
      <div class="brand-lockup">
        <div class="dot"></div>
        <div class="name">LARKWELL</div>
        <span class="tagline-lettering" role="img" aria-label="Hand-lettered brand tagline"></span>
      </div>
      <div class="band-divider"></div>
      <div class="offer">
        <div class="offer-headline">Reach more people.<br>Make more money.<br>Create more impact.</div>
        <div class="offer-body">Get your free Larkwell<br>Starter Package and our<br>marketing guide today at</div>
        <div class="offer-url">Larkwellnow.com/start</div>
      </div>
    </div>
    <div class="note-line first"></div>
    <div class="note-line second"></div>
  </section>
</main>
</body>
</html>
```